Property Developer - Simple yet Sophisticated and Sharp Business Card

We are a medium sized property developer involved mainly in townhouse developments and land subdivisions.

The company is looking for a simple, sharp and sophisticated business card that will be given to contractors, land owners, financiers etc and thus will need to look professional.

Property development related graphics and art can be used, however the card is not to be too "busy" or crowded. Our company name is Kestrel Developments which could possibly be incorporated into the graphics or artwork.

Single sided and/or double sided designs will be acceptable.

A Simple, Sophisticated, Sharp design please!

Good Luck !

```html
<!DOCTYPE html>
<html lang="en">
<head>
<meta charset="utf-8">
<title>Kestrel Developments – Business Card</title>
<link href="https://fonts.googleapis.com/css2?family=Montserrat:wght@700;800&display=swap" rel="stylesheet">
<style>
  :root {
    --backdrop: #cfcfcf;
    --cyan-core: #1fe3ff;
    --cyan-edge: #00aee0;
    --green-core: #b4ff4a;
    --green-edge: #74ff00;
    --white: #ffffff;
    --brand: #16c4ee;
  }
  * { margin: 0; padding: 0; box-sizing: border-box; }
  html, body { width: 1200px; height: 351px; overflow: hidden; background: var(--backdrop); }
  body { font-family: "Montserrat", Arial, sans-serif; }
  .canvas { position: relative; width: 1200px; height: 351px; }

  .card { position: absolute; top: 7px; width: 586px; height: 335px; border-radius: 24px; overflow: hidden; }
  .card--front { left: 12px; background: radial-gradient(ellipse at 50% 52%, var(--cyan-core) 0%, var(--cyan-edge) 75%); }
  .card--back { left: 604px; background: radial-gradient(ellipse at 40% 65%, var(--green-core) 0%, var(--green-edge) 60%); }

  .brand { position: absolute; left: 0; right: 0; display: flex; align-items: center; justify-content: center; gap: 10px;
           font-weight: 800; letter-spacing: -0.5px; text-transform: uppercase; }
  .brand__dot { width: 16px; height: 16px; border-radius: 50%; background: currentColor; }
  .brand--front { top: 196px; color: var(--white); font-size: 22px; }

  .back__head { position: absolute; left: 0; top: 0; width: 100%; height: 114px; background: var(--white); }
  .brand--back { top: 78px; color: var(--brand); font-size: 20px; }

  .person { position: absolute; right: 376px; top: 192px; color: var(--white); text-align: right; }
  .person__name { font-size: 20px; font-weight: 800; letter-spacing: -0.3px; line-height: 1; }
  .person__role { font-size: 8px; font-weight: 700; letter-spacing: 0.5px; margin-top: 2px; margin-right: 2px; }

  .divider { position: absolute; left: 252px; top: 194px; width: 1px; height: 68px; background: var(--white); }

  .contacts { position: absolute; left: 266px; top: 195px; list-style: none; color: var(--white);
              font-size: 9.5px; font-weight: 700; text-transform: uppercase; letter-spacing: 0.2px; }
  .contacts li { display: flex; align-items: center; gap: 6px; height: 18px; }
  .contacts svg { width: 11px; height: 9px; fill: none; stroke: var(--white); stroke-width: 1.4; }
</style>
</head>
<body>
<div class="canvas">
  <section class="card card--front">
    <div class="brand brand--front"><span class="brand__dot"></span>Kestrel Developments</div>
  </section>

  <section class="card card--back">
    <div class="back__head"></div>
    <div class="brand brand--back"><span class="brand__dot"></span>Kestrel Developments</div>

    <div class="person">
      <div class="person__name">YOUR NAME.....</div>
      <div class="person__role">DIRECTOR</div>
    </div>

    <div class="divider"></div>

    <ul class="contacts">
      <li><svg viewBox="0 0 11 9"><rect x="1" y="1" width="9" height="7" rx="1"/><line x1="3" y1="4" x2="8" y2="4"/></svg>+ (07) 3000 4821</li>
      <li><svg viewBox="0 0 11 9"><rect x="3" y="0.8" width="5" height="7.4" rx="1"/><line x1="5" y1="6.6" x2="6" y2="6.6"/></svg>+ (07) 3000 4822</li>
      <li><svg viewBox="0 0 11 9"><rect x="0.8" y="1.5" width="9.4" height="6" /><polyline points="0.8,1.5 5.5,5 10.2,1.5"/></svg>projects@kestreldevelopments.com</li>
      <li><svg viewBox="0 0 11 9"><path d="M1 8V4a2.5 2.5 0 0 1 5 0v4h4V4a2.5 2.5 0 0 0-2.5-2.5H3.5"/></svg>PO Box 1420 Harbourview QLD 4000</li>
    </ul>
  </section>
</div>
</body>
</html>
```